Wordpress theme website for professionals working together

My partner and I are offering business services, my wife in the energy business as mainly as member of the board of commissioners. I am working as interim manager/consultant in the accounting and finance area. Both activities are connected in one company VELMOT BV (dutch ltd). We need a CV based website. Beside this we do some financial and accounting services.

Target Market(s)

small medium business

Font styles to use
Sans Serif

Colors

Designer to choose colors to be used in the design.

Requirements
Must have
• Pictures of both members.
• CLEAN AND SIMPLE
• I LIKE BLACK & WHITE
Nice to have
• I like design like this theme: http://theme.pruxelo-example.com/resume/

```html
<!DOCTYPE html>
<html lang="en">
<head>
<meta charset="utf-8">
<title>Marit Holst – VELMOT BV</title>
<link rel="stylesheet" href="https://fonts.googleapis.com/css2?family=Montserrat:wght@400;500;600;700&family=Open+Sans:wght@400;600&display=swap">
<style>
:root{
  --ink:#111111;
  --text:#222222;
  --muted:#555555;
  --white:#ffffff;
  --grey-light:#e6e6e6;
  --grey-bar:#c4c4c4;
  --bar-dark:#1b1b1b;
  --dark:#141414;
  --card:#262626;
  --card-text:#b5b5b5;
  --brand:#1c3a78;
  --accent:#c8102e;
  --line:#cfcfcf;
}
*{margin:0;padding:0;box-sizing:border-box}
html,body{width:1200px;height:3191px;overflow:hidden;background:var(--white)}
body{font-family:"Open Sans",Arial,sans-serif;color:var(--text);position:relative}
.heading{font-family:"Montserrat",Arial,sans-serif}
section,header,footer{position:absolute;left:0;width:1200px}

/* header */
.site-header{top:0;height:66px;background:var(--white);border-bottom:1px solid #e5e5e5}
.brand{position:absolute;left:172px;top:18px;font-family:"Montserrat",Arial,sans-serif;font-weight:700;font-size:26px;color:var(--brand);letter-spacing:1px}
.nav{position:absolute;right:174px;top:27px;display:flex;gap:30px;list-style:none;font-family:"Montserrat",Arial,sans-serif;font-size:12px;letter-spacing:1px;color:#444}
.nav li.active{color:var(--ink);font-weight:600}

/* hero */
.hero{top:66px;height:557px;background:linear-gradient(90deg,#d9d9d9 0%,#e2e2e2 45%,#cfcfcf 100%)}
.hero-photo{position:absolute;right:0;top:0;width:560px;height:557px;background:linear-gradient(90deg,#d6d6d6 0%,#9c9c9c 45%,#5e5e5e 100%)}
.hero-name{position:absolute;left:170px;top:130px;font-size:50px;font-weight:500;letter-spacing:3px;color:var(--ink)}
.hero-intro{position:absolute;left:172px;top:202px;width:395px;font-size:12.5px;line-height:23px;color:var(--text)}
.signature{position:absolute;left:176px;top:378px;width:210px;height:52px;background:linear-gradient(90deg,#cfcfcf,#d9d9d9);border-radius:4px}
.profile-link{position:absolute;left:172px;top:438px;display:flex;align-items:center;gap:10px;font-size:15px;color:var(--ink);text-decoration:underline}
.profile-link .dot{width:34px;height:34px;border-radius:50%;background:var(--brand)}

/* jobs */
.jobs{top:623px;height:529px;background:var(--white)}
.section-title{position:absolute;left:0;width:1200px;text-align:center;font-family:"Montserrat",Arial,sans-serif;font-weight:700;font-size:29px;color:var(--ink);letter-spacing:1px}
.section-title .soft{color:#555;font-weight:600}
.jobs .section-title{top:58px}
.job-col{position:absolute;top:0;width:440px;height:529px}
.job-col.actual{left:172px}
.job-col.finished{left:631px}
.job-col h3{position:absolute;top:135px;left:0;font-family:"Montserrat",Arial,sans-serif;font-weight:500;font-size:19px;letter-spacing:.5px;color:var(--ink)}
.timeline{position:absolute;left:151px;top:196px;width:1px;height:262px;background:var(--line)}
.job-title{position:absolute;left:0;width:140px;font-family:"Montserrat",Arial,sans-serif;font-weight:500;font-size:15px;line-height:19px;color:var(--ink)}
.job-divider{position:absolute;left:0;width:151px;height:1px;background:var(--line)}
.node{position:absolute;left:146px;width:11px;height:11px;border-radius:50%;border:1px solid #9a9a9a;background:var(--white)}
.job-text{position:absolute;left:181px;width:225px;font-size:11px;line-height:18px;color:var(--text)}

/* skills */
.skills{top:1152px;height:551px;background:var(--grey-light)}
.skills .section-title{top:52px}
.section-intro{position:absolute;left:300px;width:600px;text-align:center;font-size:11px;line-height:19px;color:var(--text)}
.skills .section-intro{top:110px}
.skill{position:absolute;width:381px}
.skill-label{font-family:"Montserrat",Arial,sans-serif;font-weight:600;font-size:11.5px;letter-spacing:.5px;color:var(--ink);height:22px}
.skill-track{position:relative;height:32px;background:var(--grey-bar);clip-path:polygon(0 0,360px 0,381px 50%,360px 100%,0 100%)}
.skill-fill{position:absolute;left:0;top:0;height:32px;background:var(--bar-dark);z-index:0}
.skill-value{position:absolute;right:36px;top:8px;font-family:"Montserrat",Arial,sans-serif;font-size:12px;color:var(--ink);z-index:1}
.skill-value.near-tip{right:22px}

/* facts */
.facts{top:1703px;height:437px;background:linear-gradient(160deg,#1e1e1e 0%,#0e0e0e 100%)}
.fact-card{position:absolute;top:99px;height:232px;background:var(--card);text-align:center}
.fact-card svg{margin-top:38px}
.fact-card h4{margin-top:30px;font-family:"Montserrat",Arial,sans-serif;font-weight:700;font-size:14px;letter-spacing:1px;color:var(--white)}
.fact-card p{margin-top:8px;font-size:14px;line-height:20px;color:var(--card-text)}

/* portfolio */
.portfolio{top:2140px;height:758px;background:var(--white)}
.portfolio .section-title{top:60px}
.portfolio .section-intro{top:118px}
.work{position:absolute;width:279px;height:227px}
.btn{position:absolute;left:545px;top:694px;width:110px;height:32px;background:var(--ink);color:var(--white);font-family:"Montserrat",Arial,sans-serif;font-size:11px;letter-spacing:.5px;display:flex;align-items:center;justify-content:center}

/* footer */
.site-footer{top:2898px;height:293px;background:#000;color:var(--white)}
.foot-col{position:absolute;top:37px}
.foot-col h5{font-family:"Montserrat",Arial,sans-serif;font-weight:400;font-size:19px;margin-bottom:12px}
.foot-col ul{list-style:none;font-size:11px;line-height:20.5px;color:#cfcfcf}
.newsletter{position:absolute;left:708px;top:74px;width:320px;height:31px;display:flex}
.newsletter .field{flex:1;background:var(--white);border-radius:16px 0 0 16px;font-size:11px;color:#999;padding:8px 14px}
.newsletter .signup{width:84px;background:var(--accent);border-radius:0 16px 16px 0;font-family:"Montserrat",Arial,sans-serif;font-size:11px;font-weight:600;display:flex;align-items:center;justify-content:center}
.social{position:absolute;left:708px;top:137px;display:flex;gap:22px}
.social span{width:24px;height:24px;border-radius:50%;background:var(--white)}
.foot-rule{position:absolute;left:172px;top:226px;width:856px;height:1px;background:#2e2e2e}
.copyright{position:absolute;left:0;top:252px;width:1200px;text-align:center;font-size:11px;color:#cfcfcf}
</style>
</head>
<body>

<header class="site-header">
  <div class="brand">VELMOT</div>
  <ul class="nav">
    <li class="active">HOME</li><li>MARIT</li><li>SKILLS</li><li>EXPERIENCE</li><li>PORTFOLIO</li><li>EDUCATION</li><li>CONTACT</li>
  </ul>
</header>

<section class="hero">
  <div class="hero-photo" role="img" aria-label="Black and white portrait photo of Marit Holst"></div>
  <h1 class="hero-name heading">MARIT HOLST</h1>
  <p class="hero-intro">Sed ut perspiciatis unde omnis iste natus error sit voluptatem accusantium doloremque laudantium, totam rem aperiam, eaque ipsa quae ab illo inventore veritatis et quasi architecto beatae vitae dicta sunt explicabo. Nemo enim ipsam voluptatem quia voluptas sit aspernatur aut odit aut fugit, sed quia consequuntur magni dolores eos qui ratione voluptatem sequi nesciunt. Neque porro quisquam est, qui dolorem ipsum quia dolor sit amet, consectetur.</p>
  <div class="signature" role="img" aria-label="Handwritten signature of Marit Holst"></div>
  <div class="profile-link"><span class="dot"></span>Profile</div>
</section>

<section class="jobs">
  <h2 class="section-title">MARIT HOLST <span class="soft">JOBS</span></h2>

  <div class="job-col actual">
    <h3>ACTUAL JOBS</h3>
    <div class="timeline"></div>
    <div class="job-title" style="top:209px">Director<br>Veltra</div>
    <div class="job-divider" style="top:271px"></div>
    <div class="node" style="top:223px"></div>
    <p class="job-text" style="top:198px">Sed ut perspiciatis unde omnis iste naus error sit voluptatem accusa ntiumdolor emque laudantium, totam rem.</p>
    <div class="job-title" style="top:304px">Ravelo</div>
    <div class="node" style="top:308px"></div>
    <p class="job-text" style="top:285px">Sed ut perspiciatis unde omnis iste ntus error sit voluptatem accusa ntiumdolor emque laudantium, totam rem.</p>
    <p class="job-text" style="top:360px">Sed ut perspiciatis unde omnis iste nats error sit voluptatem accusa ntiumdolor emque laudantium, totam rem.ed upers piciatis unde omnis iste natus error sit voluptatem accusa ntiumdolor.</p>
  </div>

  <div class="job-col finished">
    <h3>FINISHED JOBS</h3>
    <div class="timeline"></div>
    <div class="job-title" style="top:209px">Director<br>Pelgon</div>
    <div class="job-divider" style="top:271px"></div>
    <div class="node" style="top:223px"></div>
    <p class="job-text" style="top:198px">Sed ut perspiciatis unde omnis iste natus error sit voluptatem accusa ntiumdolor emque laudantium, totam rem.</p>
    <div class="job-title" style="top:304px">Advisor Gas</div>
    <div class="job-divider" style="top:362px"></div>
    <div class="node" style="top:308px"></div>
    <p class="job-text" style="top:285px">Sed ut perspiciatis unde omnis iste natus error sit voluptatem accusa ntiumdolor emque laudantium, totam rem.</p>
    <div class="job-title" style="top:391px">Oipoip o<br>loremiop</div>
    <div class="node" style="top:402px"></div>
    <p class="job-text" style="top:382px">Sed ut perspiciatis unde omnis iste natus error sit voluptatem accusa ntiumdolor emque laudantium, totam rem.</p>
  </div>
</section>

<section class="skills">
  <h2 class="section-title">SKILLS</h2>
  <p class="section-intro">Sed ut perspiciatis unde omnis iste ntus error sit voluptatem accusa ntiumdolor emque laudantium, totam remd ut perspiciatis unde omnis iste nats error sit voluptatem accusa ntiumdolor emque lauda</p>

  <div class="skill" style="left:172px;top:187px"><div class="skill-label">GENERAL MANAGEMENT</div><div class="skill-track"><div class="skill-fill" style="width:287px"></div><span class="skill-value">80%</span></div></div>
  <div class="skill" style="left:172px;top:256px"><div class="skill-label">ENERGY KNOWLEDGE</div><div class="skill-track"><div class="skill-fill" style="width:252px"></div><span class="skill-value">50%</span></div></div>
  <div class="skill" style="left:172px;top:326px"><div class="skill-label">GAS KNOWLEDGE</div><div class="skill-track"><div class="skill-fill" style="width:327px"></div><span class="skill-value near-tip">90%</span></div></div>
  <div class="skill" style="left:172px;top:395px"><div class="skill-label">PEOPLE MANAGEMENT</div><div class="skill-track"><div class="skill-fill" style="width:204px"></div><span class="skill-value">40%</span></div></div>

  <div class="skill" style="left:643px;top:187px"><div class="skill-label">PROJECT MANAGEMENT</div><div class="skill-track"><div class="skill-fill" style="width:185px"></div><span class="skill-value">30%</span></div></div>
  <div class="skill" style="left:643px;top:256px"><div class="skill-label">TEAM PLAYER</div><div class="skill-track"><div class="skill-fill" style="width:300px"></div><span class="skill-value">80%</span></div></div>
  <div class="skill" style="left:643px;top:326px"><div class="skill-label">TROUBLE SHOOTER</div><div class="skill-track"><div class="skill-fill" style="width:268px"></div><span class="skill-value">70%</span></div></div>
  <div class="skill" style="left:643px;top:395px"><div class="skill-label">ETC.</div><div class="skill-track"><div class="skill-fill" style="width:225px"></div><span class="skill-value">40%</span></div></div>
</section>

<section class="facts">
  <div class="fact-card" style="left:172px;width:271px">
    <svg width="68" height="56" viewBox="0 0 68 56" fill="none" stroke="#fff" stroke-width="2.2" stroke-linejoin="round">
      <path d="M34 10 C26 4 14 4 4 7 V48 C14 45 26 45 34 51 Z"/>
      <path d="M34 10 C42 4 54 4 64 7 V48 C54 45 42 45 34 51 Z"/>
    </svg>
    <h4>EDUCATION</h4>
    <p>HVU<br>Atheneum B</p>
  </div>
  <div class="fact-card" style="left:466px;width:270px">
    <svg width="64" height="60" viewBox="0 0 64 60" fill="none" stroke="#fff" stroke-width="2.2" stroke-linecap="round" stroke-linejoin="round">
      <path d="M10 52 L40 22"/>
      <path d="M6 56 L14 48"/>
      <path d="M38 10 C42 4 52 4 56 8 L48 16 L52 20 L60 12 C62 20 56 28 48 26 L16 56 C13 59 8 54 11 51 L42 20 C40 16 36 14 38 10 Z"/>
      <path d="M10 6 L20 16 L26 16 L46 36 L40 42 L20 22 L20 16"/>
      <path d="M46 36 L58 48 C60 51 57 56 53 54 L40 42"/>
    </svg>
    <h4>WORKED FOR</h4>
    <p>Pelgon<br>HVU</p>
  </div>
  <div class="fact-card" style="left:755px;width:273px">
    <svg width="56" height="60" viewBox="0 0 56 60" fill="none" stroke="#fff" stroke-width="2.2" stroke-linejoin="round">
      <rect x="8" y="4" width="40" height="52" rx="3"/>
      <path d="M8 40 H48 M8 46 H48"/>
      <rect x="15" y="12" width="26" height="6"/>
      <rect x="15" y="23" width="26" height="6"/>
    </svg>
    <h4>OTHER</h4>
    <p>Reading</p>
  </div>
</section>

<section class="portfolio">
  <h2 class="section-title">PORTFOLIO</h2>
  <p class="section-intro">Sed ut perspiciatis unde omnis iste ntus error sit voluptatem accusa ntiumdolor emque laudantium, totam remd ut perspiciatis unde omnis iste nats error sit voluptatem accusa ntiumdolor emque lauda</p>

  <div class="work" style="left:172px;top:194px;background:linear-gradient(135deg,#e9ebee,#b9c0c9 60%,#4a74b8)" role="img" aria-label="Photo of business people signing documents at a desk"></div>
  <div class="work" style="left:460px;top:194px;background:radial-gradient(circle at 45% 35%,#d9b640 0%,#5a4a22 30%,#1c1c1c 70%)" role="img" aria-label="Photo of a hand holding a glowing light bulb with a brain"></div>
  <div class="work" style="left:747px;top:194px;background:radial-gradient(circle at 50% 45%,#f3d9a6 0%,#b7794a 40%,#3b2418 100%)" role="img" aria-label="Photo of hands holding an open book with warm light"></div>
  <div class="work" style="left:172px;top:431px;background:linear-gradient(135deg,#b8a27c,#8c744f 55%,#d78a2a)" role="img" aria-label="Illustration of a businesswoman pushing a rising orange arrow"></div>
  <div class="work" style="left:460px;top:431px;background:linear-gradient(135deg,#2d3f66,#c9ccd1 55%,#eef0f3)" role="img" aria-label="Photo of people reviewing charts on paper"></div>
  <div class="work" style="left:747px;top:431px;background:linear-gradient(180deg,#4d5a70 0%,#c98b5e 55%,#3e3a3d 100%)" role="img" aria-label="Photo of an industrial gas pipeline at sunset"></div>

  <div class="btn">VIEW MORE</div>
</section>

<footer class="site-footer">
  <div class="foot-col" style="left:172px"><h5>Company</h5><ul><li>Sed ut perspiciatis</li><li>Unde omnis iste</li><li>Voluptatem</li><li>Accusantium</li><li>Doloremque</li><li>Laudantium</li></ul></div>
  <div class="foot-col" style="left:352px"><h5>About</h5><ul><li>Sed ut perspiciatis</li><li>Unde omnis iste</li><li>Voluptatem</li><li>Accusantium</li><li>Doloremque</li><li>Laudantium</li></ul></div>
  <div class="foot-col" style="left:517px"><h5>Links</h5><ul><li>Sed ut perspiciatis</li><li>Unde omnis iste</li><li>Voluptatem</li><li>Accusantium</li><li>Doloremque</li><li>Laudantium</li></ul></div>
  <div class="foot-col" style="left:708px"><h5>Newsletter</h5></div>
  <div class="newsletter"><div class="field">Email</div><div class="signup">SIGN UP</div></div>
  <div class="social"><span></span><span></span><span></span><span></span></div>
  <div class="foot-rule"></div>
  <p class="copyright">© 2018 All Rights Are Reserved.Terms of Use | Privacy Policy</p>
</footer>

</body>
</html>
```